Newsletter Ad

I am looking for someone to design an advertisement for a mother's club newsletter. 4" wide X by 5" tall (and 2.5" wide X 5" tall if possible).

I'm a psychotherapist, so want the ad to look professional, but modern. I have a logo with my photo attached that can be incorporated into the design. The colors of my website are turquoise and white. I'd like to keep with that theme...so maybe some turquoise blocking to match the logo font color.

I'm uploading a logo as well as an ad draft with the content I'd like listed in the ad.

```html
<!DOCTYPE html>
<html lang="en">
<head>
<meta charset="utf-8">
<title>Dana Rowell, MA, MFT – Newsletter Ad</title>
<link href="https://fonts.googleapis.com/css2?family=Questrial&display=swap" rel="stylesheet">
<style>
  :root {
    --teal: #2b9a90;
    --teal-name: #2a9a92;
    --white: #ffffff;
    --off-white: #f6f9fa;
    --ink: #1c1c1c;
    --grey: #555555;
    --license-ink: #16302d;
  }
  html, body {
    margin: 0;
    padding: 0;
    overflow: hidden;
    background: var(--white);
  }
  .ad {
    position: relative;
    width: 961px;
    height: 1200px;
    overflow: hidden;
    background: var(--white);
    font-family: "Questrial", "Century Gothic", sans-serif;
  }
  .portrait {
    position: absolute;
    left: 0;
    top: 0;
    width: 274px;
    height: 374px;
    background: linear-gradient(160deg, #2e2b27 0%, #6b5540 45%, #b8997a 75%, #3a3a32 100%);
  }
  .header-name {
    position: absolute;
    left: 300px;
    top: 80px;
    margin: 0;
    font-weight: 400;
    font-size: 64px;
    letter-spacing: 1px;
    color: var(--teal-name);
    line-height: 1;
  }
  .tagline {
    position: absolute;
    left: 274px;
    width: 616px;
    top: 246px;
    margin: 0;
    text-align: center;
    font-size: 35px;
    line-height: 49px;
    color: var(--grey);
  }
  .services {
    position: absolute;
    left: 0;
    top: 374px;
    width: 961px;
    height: 554px;
    background: var(--teal);
  }
  .services ul {
    list-style: none;
    margin: 0;
    padding: 0;
    position: absolute;
    top: 43px;
    width: 100%;
    text-align: center;
  }
  .services li {
    color: var(--white);
    font-size: 39px;
    line-height: 60px;
  }
  .contact {
    position: absolute;
    left: 0;
    top: 928px;
    width: 961px;
    height: 206px;
    background: var(--off-white);
    text-align: center;
  }
  .contact p {
    margin: 0;
    color: var(--ink);
    font-size: 36px;
    line-height: 48px;
  }
  .contact .lines {
    position: absolute;
    top: 9px;
    width: 100%;
  }
  .footer-band {
    position: absolute;
    left: 0;
    top: 1134px;
    width: 961px;
    height: 66px;
    background: var(--teal);
  }
  .license {
    position: absolute;
    right: 27px;
    top: 14px;
    margin: 0;
    font-size: 25px;
    color: var(--license-ink);
  }
</style>
</head>
<body>
  <div class="ad">
    <div class="portrait" role="img" aria-label="Portrait photo of the therapist"></div>
    <h1 class="header-name">DANA ROWELL, MA, MFT</h1>
    <p class="tagline">Psychotherapy for Individuals,<br>Couples and Families</p>

    <section class="services">
      <ul>
        <li>Parenting</li>
        <li>Depression</li>
        <li>Anxiety</li>
        <li>Life Transitions</li>
        <li>Divorce</li>
        <li>Couples Issues</li>
        <li>Women’s Issues</li>
        <li>Attachment and Neuroscience</li>
      </ul>
    </section>

    <section class="contact">
      <div class="lines">
        <p>148 Harbor Lane, Sausalito, CA 94965</p>
        <p>www.danarowell.com</p>
        <p>dana@danarowell.com</p>
        <p>415.555.0183</p>
      </div>
    </section>

    <footer class="footer-band">
      <p class="license">License# MFC48203</p>
    </footer>
  </div>
</body>
</html>
```